Lanternfield Drinks business cards

We need a business card design for our new logo. The company is modern, progressive, professional, yet approachable. The key products are ready to drink bottles and cans of coffee based beverages.
These cards will be a critical part of the first impression made by our sales organization, business development team, and all external facing personnel.
Card can be a vertical or horizontal orientation.

Target Market(s)

Customers, suppliers, business partners

Industry/Entity Type

Business

Contact Information for Business Card

Business cards should feature Company Name and Logo.

Font styles to use
Serif

Colors

Designer to choose colors to be used in the design.

Requirements
Must have
• Strong readability of Name, phone #, mobile number and email address.
• Job title, website url, Street Address, and other details can be secondary level readability.
Nice to have
• High impact, simplistic quality design.
• Ok to utilize the 'H in the box' separate from the company name

```html
<!DOCTYPE html>
<html lang="en">
<head>
<meta charset="utf-8">
<title>Lanternfield Drinks business cards</title>
<link rel="stylesheet" href="https://fonts.googleapis.com/css2?family=Cinzel:wght@600&family=Cormorant+Garamond:wght@500&family=Montserrat:wght@300;400&display=swap">
<style>
  :root {
    --backdrop: #d9d9d9;
    --card: #1f1f20;
    --accent: #e8401c;
    --accent-soft: #c9381a;
    --light: #d4d4d4;
    --muted: #bdbdbd;
  }
  * { box-sizing: border-box; margin: 0; padding: 0; }
  html, body { width: 1200px; height: 1021px; overflow: hidden; }
  body {
    background: var(--backdrop);
    display: flex;
    flex-direction: column;
    align-items: center;
    justify-content: center;
    gap: 48px;
  }
  .card {
    position: relative;
    width: 760px;
    height: 434px;
    background: var(--card);
    box-shadow: 0 10px 28px rgba(0,0,0,.28);
  }
  .brand {
    display: flex;
    align-items: center;
    gap: 18px;
  }
  .brand-square {
    width: 46px;
    height: 46px;
    border: 3px solid var(--accent);
    flex: none;
  }
  .brand-name {
    font-family: "Cinzel", serif;
    font-weight: 600;
    color: var(--accent);
    letter-spacing: 1px;
    white-space: nowrap;
  }
  .card-front {
    display: flex;
    align-items: center;
    justify-content: center;
  }
  .card-front .brand-name { font-size: 46px; }
  .card-front .brand-square { width: 64px; height: 64px; border-width: 4px; }

  .card-back .brand {
    position: absolute;
    top: 54px;
    right: 52px;
  }
  .card-back .brand-name { font-size: 28px; }
  .card-back .brand-square { width: 38px; height: 38px; }

  .person {
    position: absolute;
    left: 70px;
    top: 176px;
  }
  .person-name {
    font-family: "Cormorant Garamond", serif;
    font-weight: 500;
    font-size: 30px;
    color: var(--light);
    letter-spacing: 1px;
  }
  .person-title {
    font-family: "Cormorant Garamond", serif;
    font-weight: 500;
    font-size: 19px;
    color: var(--accent-soft);
    letter-spacing: 1px;
    margin-top: 2px;
  }
  .rule {
    width: 62px;
    height: 3px;
    background: var(--accent);
  }
  .rule-top { position: absolute; left: 70px; top: 270px; }
  .rule-bottom { position: absolute; left: 70px; top: 392px; }
  .contacts {
    position: absolute;
    left: 70px;
    top: 294px;
    list-style: none;
    font-family: "Montserrat", sans-serif;
    font-weight: 300;
    font-size: 15px;
    color: var(--light);
  }
  .contacts li {
    display: flex;
    align-items: center;
    gap: 12px;
    height: 28px;
  }
  .contacts svg { width: 16px; height: 16px; flex: none; }
  .website {
    position: absolute;
    right: 52px;
    bottom: 150px;
    font-family: "Montserrat", sans-serif;
    font-weight: 400;
    font-size: 14px;
    color: var(--accent-soft);
  }
</style>
</head>
<body>
  <section class="card card-front">
    <div class="brand">
      <span class="brand-square"></span>
      <span class="brand-name">LANTERNFIELD DRINKS</span>
    </div>
  </section>

  <section class="card card-back">
    <div class="brand">
      <span class="brand-square"></span>
      <span class="brand-name">LANTERNFIELD DRINKS</span>
    </div>

    <div class="person">
      <p class="person-name">YOUR NAME</p>
      <p class="person-title">JOB TITLE</p>
    </div>

    <span class="rule rule-top"></span>
    <ul class="contacts">
      <li>
        <svg viewBox="0 0 16 16" aria-hidden="true"><path fill="#e8401c" d="M2 5c0-2 2-3 6-3s6 1 6 3v1h-3V5H5v1H2zM3 7h10l1 7H2zm5 2a2 2 0 100 4 2 2 0 000-4z"/></svg>
        <span>+971 XXXXXXX</span>
      </li>
      <li>
        <svg viewBox="0 0 16 16" aria-hidden="true"><rect x="4.5" y="1.5" width="7" height="13" rx="1.2" fill="none" stroke="#e8401c" stroke-width="1.5"/><circle cx="8" cy="12" r=".9" fill="#e8401c"/></svg>
        <span>+971 YYYYYYY</span>
      </li>
      <li>
        <svg viewBox="0 0 16 16" aria-hidden="true"><rect x="1" y="3" width="14" height="10" fill="#e8401c"/><path d="M1.5 3.5L8 9l6.5-5.5" fill="none" stroke="#1f1f20" stroke-width="1.3"/></svg>
        <span>x@y.com</span>
      </li>
    </ul>
    <span class="rule rule-bottom"></span>

    <p class="website">www.yourwebsite.com</p>
  </section>
</body>
</html>
```